Residential Remodeling Contractor needs updated business card

I need a new design for my business card.
Name of the company is Ridgefell Construction. I need a card that commands presence, strength, integrity. I have been in business for 28 years. I am a Residential Remodeling Contractor that covers all aspects of a residential remodel and build.

```html
<!DOCTYPE html>
<html lang="en">
<head>
<meta charset="utf-8">
<title>Ridgefell Construction — Business Card</title>
<link href="https://fonts.googleapis.com/css2?family=Cinzel:wght@600&family=Arimo:wght@400;700&display=swap" rel="stylesheet">
<style>
  :root {
    --navy: #1a3f7d;
    --white: #ffffff;
    --stage: #d9dadc;
    --soft: #b9c4dc;
  }
  * { margin: 0; padding: 0; box-sizing: border-box; }
  html, body { width: 1200px; height: 901px; overflow: hidden; }
  body { background: var(--stage); position: relative; font-family: "Arimo", Arial, sans-serif; }

  .card {
    position: absolute;
    width: 560px; height: 320px;
    border-radius: 22px;
    overflow: hidden;
    background: var(--navy);
    box-shadow: 0 8px 24px rgba(0,0,0,.18);
  }
  .card--front { left: 40px; top: 100px; }
  .card--back  { left: 600px; top: 480px; }

  .company-name {
    position: absolute;
    font-family: "Arimo", Arial, sans-serif;
    font-weight: 700;
    line-height: 1;
    white-space: nowrap;
  }
  .card--front .company-name {
    color: var(--white);
    left: 0; right: 0; top: 140px;
    text-align: center;
    font-size: 38px;
  }

  .back-art { position: absolute; inset: 0; }
  .card--back .company-name {
    color: var(--navy);
    left: 240px; top: 62px;
    font-size: 24px;
  }

  .contact {
    position: absolute; left: 40px; bottom: 30px;
    color: var(--white);
  }
  .contact__name {
    font-family: "Cinzel", Georgia, serif; font-weight: 600;
    font-size: 19px; letter-spacing: .04em; text-transform: uppercase;
  }
  .contact__role { font-size: 13px; margin-top: 2px; }
  .contact__rule { width: 16px; height: 1px; background: var(--white); margin: 8px 0; }
  .contact__list { list-style: none; font-size: 12.5px; }
  .contact__item { display: flex; align-items: center; gap: 8px; height: 18px; }
  .contact__icon { width: 11px; height: 11px; flex: none; }
</style>
</head>
<body>

  <section class="card card--front" aria-label="Card front">
    <h1 class="company-name">Ridgefell Construction</h1>
  </section>

  <section class="card card--back" aria-label="Card back">
    <svg class="back-art" viewBox="0 0 560 320" preserveAspectRatio="none" aria-hidden="true">
      <defs>
        <linearGradient id="swoosh" x1="0" x2="1" y1="0" y2="0">
          <stop offset="0" stop-color="#ffffff" stop-opacity=".2"/>
          <stop offset=".3" stop-color="#1a3f7d"/>
          <stop offset="1" stop-color="#1a3f7d"/>
        </linearGradient>
      </defs>
      <rect width="560" height="320" fill="var(--navy)"/>
      <path d="M150 0 H560 V180 C470 205 330 215 260 160 C210 120 175 60 150 0 Z" fill="var(--white)"/>
      <path d="M150 0 C178 70 215 130 265 170 C330 222 470 212 560 186" fill="none" stroke="url(#swoosh)" stroke-width="7"/>
      <path d="M160 0 C185 62 218 118 266 156 C330 204 470 196 560 172" fill="none" stroke="var(--soft)" stroke-width="1.2" opacity=".6"/>
    </svg>

    <h2 class="company-name">Ridgefell Construction</h2>

    <div class="contact">
      <p class="contact__name">Dale Whitcombe</p>
      <p class="contact__role">Owner &amp; Manager</p>
      <div class="contact__rule"></div>
      <ul class="contact__list">
        <li class="contact__item">
          <svg class="contact__icon" viewBox="0 0 12 12" aria-hidden="true"><path d="M2 1h3l1 3-2 1a7 7 0 0 0 3 3l1-2 3 1v3c-6 0-10-4-10-10z" fill="#fff"/></svg>
          555 214 7730
        </li>
        <li class="contact__item">
          <svg class="contact__icon" viewBox="0 0 12 12" aria-hidden="true"><rect x="3" y="0.5" width="6" height="11" rx="1.2" fill="none" stroke="#fff"/><circle cx="6" cy="9.5" r=".7" fill="#fff"/></svg>
          555-318-6042
        </li>
        <li class="contact__item">
          <svg class="contact__icon" viewBox="0 0 12 12" aria-hidden="true"><rect x=".5" y="2.5" width="11" height="7" fill="none" stroke="#fff"/><path d="M.5 2.5 6 7l5.5-4.5" fill="none" stroke="#fff"/></svg>
          info@ridgefellconstruction.com
        </li>
        <li class="contact__item">
          <svg class="contact__icon" viewBox="0 0 12 12" aria-hidden="true"><circle cx="6" cy="6" r="5.2" fill="none" stroke="#fff"/><path d="M1 6h10M6 .8c-3 3-3 7.4 0 10.4M6 .8c3 3 3 7.4 0 10.4" fill="none" stroke="#fff" stroke-width=".8"/></svg>
          www.ridgefellconstruction.com
        </li>
      </ul>
    </div>
  </section>

</body>
</html>
```